Bluecrest Learning Corps by graduating students from college in two years

Based on the logo design, create stationary and business cards for
Dr. Venrel T Oskamp, CEO, (703) 482-1736
and Marisa Deltoft, Respresentative, (301) 647-2208
Address: 4719 Pellham Court, Dunmore Hollow, VA 22174
Incorporate elelments of the logo

Target Market(s)

USA

Font styles to use
Other font styles liked:
• match with the logo type style

```html
<!DOCTYPE html>
<html lang="en">
<head>
<meta charset="utf-8">
<title>Bluecrest Learning Corps – Stationery</title>
<link href="https://fonts.googleapis.com/css2?family=Tinos:wght@400;700&family=Source+Sans+3:wght@400&display=swap" rel="stylesheet">
<style>
  :root {
    --navy: #1f2357;
    --gold: #f6c432;
    --ink: #4a4a4a;
    --muted: #5b5b5b;
    --paper: #ffffff;
    --backdrop: #e8e5e0;
    --serif: "Tinos", "Times New Roman", serif;
    --sans: "Source Sans 3", "Helvetica Neue", Arial, sans-serif;
  }
  * { box-sizing: border-box; margin: 0; padding: 0; }
  html, body { width: 1200px; height: 1067px; overflow: hidden; }
  body { background: var(--backdrop); position: relative; font-family: var(--sans); color: var(--ink); }

  .card {
    position: absolute; background: var(--paper); border-radius: 24px;
    box-shadow: 0 3px 10px rgba(0,0,0,.18);
  }
  .card-front { left: 74px; top: 249px; width: 468px; height: 268px; display: flex; align-items: center; justify-content: center; }
  .card-back { left: 77px; top: 546px; width: 463px; height: 264px; }

  .brand { display: flex; align-items: center; gap: 10px; font-family: var(--serif); font-weight: 700; color: var(--navy); }
  .brand-dot { border-radius: 50%; background: var(--gold); flex: none; }
  .card-front .brand { font-size: 24px; }
  .card-front .brand-dot { width: 26px; height: 26px; }

  .card-back .brand { position: absolute; left: 26px; top: 114px; width: 140px; font-size: 14px; line-height: 1.15; gap: 7px; }
  .card-back .brand-dot { width: 16px; height: 16px; }
  .card-back .divider { position: absolute; left: 188px; top: 78px; width: 2px; height: 108px; background: var(--gold); }
  .card-back .details { position: absolute; left: 211px; top: 74px; font-family: var(--serif); color: #333; }
  .holder-name { font-size: 23px; font-weight: 700; color: var(--gold); line-height: 1; white-space: nowrap; }
  .holder-role { font-size: 13px; margin-top: 5px; }
  .address { font-size: 13px; line-height: 19px; margin-top: 12px; }
  .phone { font-size: 13px; margin-top: 12px; display: flex; align-items: center; gap: 6px; }
  .phone svg { width: 11px; height: 9px; fill: var(--gold); }

  .letterhead {
    position: absolute; left: 573px; top: 143px; width: 551px; height: 780px;
    background: var(--paper); box-shadow: 0 3px 10px rgba(0,0,0,.18);
  }
  .letterhead .brand { position: absolute; left: 52px; top: 38px; width: 140px; font-size: 14px; line-height: 1.15; gap: 7px; }
  .letterhead .brand-dot { width: 16px; height: 16px; }
  .lh-contact { position: absolute; left: 376px; top: 45px; padding-left: 13px; border-left: 1px solid var(--gold); font-family: var(--serif); font-size: 10px; color: #333; line-height: 14px; }
  .lh-contact .phones { margin-top: 8px; }
  .lh-contact .phone { font-size: 10px; margin-top: 0; gap: 4px; }
  .lh-contact .phone svg { width: 8px; height: 7px; }

  .recipient { position: absolute; left: 52px; top: 182px; font-size: 8.3px; line-height: 14px; color: var(--muted); }
  .recipient-name { font-size: 11px; letter-spacing: .2px; margin-bottom: 1px; }

  .letter-body { position: absolute; left: 52px; top: 276px; width: 447px; font-size: 8.2px; line-height: 13.5px; color: var(--muted); text-align: justify; }
  .letter-body p + p { margin-top: 12px; }

  .signoff { position: absolute; left: 52px; top: 578px; font-size: 9px; color: var(--muted); }
  .signoff-name { font-size: 11px; margin-top: 30px; }

  .lh-footer { position: absolute; left: 52px; top: 749px; font-family: var(--serif); font-size: 9px; color: #333; white-space: nowrap; }
  .lh-stripes { position: absolute; left: 298px; top: 752px; width: 253px; height: 10px; }
</style>
</head>
<body>

  <section class="card card-front" aria-label="Business card front">
    <div class="brand"><span class="brand-dot"></span><span>Bluecrest Learning Corps</span></div>
  </section>

  <section class="card card-back" aria-label="Business card back">
    <div class="brand"><span class="brand-dot"></span><span>Bluecrest Learning Corps</span></div>
    <div class="divider"></div>
    <div class="details">
      <div class="holder-name">Dr. Venrel T Oskamp</div>
      <div class="holder-role">CEO</div>
      <div class="address">4719 Pellham Court,<br>Dunmore Hollow, VA 22174</div>
      <div class="phone"><svg viewBox="0 0 12 10"><path d="M1 3c0-2 10-2 10 0v1H8.5V3h-5v1H1zM3 4h6l2 5H1z"/></svg>(703) 482-1736</div>
    </div>
  </section>

  <article class="letterhead" aria-label="Letterhead">
    <div class="brand"><span class="brand-dot"></span><span>Bluecrest Learning Corps</span></div>
    <div class="lh-contact">
      <div>4719 Pellham Court,<br>Dunmore Hollow, VA 22174</div>
      <div class="phones">
        <div class="phone"><svg viewBox="0 0 12 10"><path d="M1 3c0-2 10-2 10 0v1H8.5V3h-5v1H1zM3 4h6l2 5H1z"/></svg>(703) 482-1736</div>
        <div class="phone"><svg viewBox="0 0 12 10"><path d="M1 3c0-2 10-2 10 0v1H8.5V3h-5v1H1zM3 4h6l2 5H1z"/></svg>(301) 647-2208</div>
      </div>
    </div>

    <div class="recipient">
      <div class="recipient-name">ELENA VARSHOLT</div>
      <div>Chief Exective Officer</div>
      <div>City/State, Zip Code</div>
    </div>

    <div class="letter-body">
      <p>Proin gravida nibh vel velit auctor aliquet. Aenean sollicitudin, lorem quis bibendum auctor, nisi elit consequat ipsum, nec sagittis sem nibh id elit. Duis sed odio sit amet nibh vulputate cursus a sit amet mauris. Morbi accumsan ipsum velit. Nam nec tellus a odio tincidunt auctor a ornare odio. Sed non mauris vitae erat consequat auctor eu in elit. Class aptent taciti sociosqu ad litora torquent ugue. Sed non neque elit. Sed ut imperdiet nisi. Proin condimentum fermentum nunc. Etiam pharetra, imperdiet nisi. Proin condimentum fermentum nunc. Etiam pharetra, erat sed fermentum feugiat, velit mauris egestas quam, ut aliquam massa nisl quis neque. Suspendisse in orci enim.</p>
      <p>This is Photoshop's version of Lorem Ipsum. Proin gravida nibh vel velit auctor aliquet. Aenean sollicitudin, lorem quis bibendum auctor, nisi elit consequat ipsum, nec sagittis sem nibh id elit. Duis sed odio sit amet nibh vulputate cursus a sit amet mauris. Mo rbi accumsan ipsum velit. Nam nec tellus a odio tincidunt auctor a ornare odio. Sed non mauris vitae erat consequat auctor eu in elit. Class aptt consequat auctor eu in elit. Class aptent taciti sociosqu ad litora torquent per conubia nostra, per inceptos himenaeos. Mauris in erat justo.</p>
      <p>Nullam ac urna eu felis dapibus condimentum sit amet a augue. Sed non neque elit. Sed ut imperdiet nisi. Proin condimentum fermentum nunc. Etiam pharetra, erat sed fermentum feugiat, velit mauris egestas quam.Nullam ac urna eu felis dapibus condimentum sit amet a aug pharetra, erat sed fermentum feugiat, velit mauris egestas quam.Nullam ac urna eu felis dapibus condimentum sit amet a augue. Sed non neque elit. Sed ut imperdiet nisi. Proin condimentum fermentum nunc.</p>
    </div>

    <div class="signoff">
      <div>Sincerely,</div>
      <div class="signoff-name">Corin Ashby</div>
    </div>

    <div class="lh-footer">Dr. Venrel T Oskamp, CEO / Marisa Deltoft, Respresentative</div>
    <svg class="lh-stripes" viewBox="0 0 253 10" preserveAspectRatio="none" aria-hidden="true">
      <polygon points="8,0 30,0 22,10 0,10" fill="var(--gold)"/>
      <polygon points="34,0 56,0 48,10 26,10" fill="var(--navy)"/>
      <polygon points="60,0 253,0 253,10 52,10" fill="var(--gold)"/>
    </svg>
  </article>

</body>
</html>
```